Create a memorable Stationary for Security Software Company

Velbrantix is the worldwide leader in securing the Internet. Making Internet communications and critical data secure, reliable and available everywhere has been and continues to be our ongoing vision. We are committed to staying focused on real customer needs and to developing new and innovative security solutions that redefine the security landscape.

Industry/Entity Type

Internet

Font styles to use
Serif
Sans Serif
Script

Colors
0792cd
33a6d7
85cae6

```html
<!DOCTYPE html>
<html lang="en">
<head>
<meta charset="utf-8">
<title>Velbrantix Business Card</title>
<link href="https://fonts.googleapis.com/css2?family=Open+Sans:wght@400;600;700&display=swap" rel="stylesheet">
<style>
  :root {
    --brand-blue: #0792cd;
    --brand-mid: #33a6d7;
    --brand-light: #85cae6;
    --ink: #333333;
    --paper: #ffffff;
    --backdrop: #e6e8ea;
  }
  * { box-sizing: border-box; margin: 0; padding: 0; }
  html, body { width: 1200px; height: 1120px; overflow: hidden; }
  body {
    background: var(--backdrop);
    font-family: "Open Sans", sans-serif;
    position: relative;
  }
  .card {
    position: absolute;
    left: 150px;
    width: 900px;
    height: 514px;
    background: var(--paper);
    overflow: hidden;
    box-shadow: 0 6px 22px rgba(0,0,0,0.18);
  }
  .card--front { top: 26px; border-bottom: 6px solid var(--brand-blue); }
  .card--back { top: 580px; }

  .wordmark {
    display: flex;
    align-items: center;
    gap: 18px;
    color: var(--brand-mid);
    font-weight: 700;
    letter-spacing: 0.5px;
  }
  .wordmark__dot {
    border-radius: 50%;
    background: var(--brand-mid);
    flex: none;
  }
  .card--front .wordmark {
    position: absolute;
    left: 0; right: 0; top: 170px;
    justify-content: center;
    font-size: 70px;
  }
  .card--front .wordmark__dot { width: 54px; height: 54px; }
  .front__url {
    position: absolute;
    left: 0; right: 0; top: 355px;
    text-align: center;
    font-size: 26px;
    letter-spacing: 4px;
    color: var(--ink);
  }

  .card--back .wordmark {
    position: absolute;
    left: 55px; top: 228px;
    font-size: 52px;
    gap: 14px;
  }
  .card--back .wordmark__dot { width: 40px; height: 40px; }
  .back__panel { position: absolute; inset: 0; }
  .contact {
    position: absolute;
    right: 40px; top: 62px;
    text-align: right;
    color: var(--paper);
  }
  .contact__name { font-size: 25px; font-weight: 700; line-height: 1.2; }
  .contact__title { font-size: 21px; line-height: 1.3; margin-bottom: 38px; }
  .contact__list { list-style: none; font-size: 19px; line-height: 1.55; }
  .contact__list li { display: flex; justify-content: flex-end; align-items: center; gap: 10px; }
  .contact__list li.contact__address { align-items: flex-start; margin-top: 10px; line-height: 1.35; }
  .contact__list svg { width: 18px; height: 18px; flex: none; fill: var(--paper); }
  .contact__address svg { width: 22px; height: 22px; margin-top: 2px; }
</style>
</head>
<body>

<section class="card card--front" aria-label="Card front">
  <div class="wordmark"><span class="wordmark__dot"></span>Velbrantix</div>
  <p class="front__url">www.velbrantix.com.com</p>
</section>

<section class="card card--back" aria-label="Card back">
  <svg class="back__panel" viewBox="0 0 900 514" width="900" height="514" aria-hidden="true">
    <circle cx="752" cy="257" r="322" fill="var(--brand-blue)"/>
    <circle cx="778" cy="257" r="310" fill="var(--paper)"/>
    <circle cx="785" cy="257" r="302" fill="var(--brand-blue)"/>
  </svg>

  <div class="wordmark"><span class="wordmark__dot"></span>Velbrantix</div>

  <div class="contact">
    <p class="contact__name">Your Name</p>
    <p class="contact__title">Title</p>
    <ul class="contact__list">
      <li>
        <svg viewBox="0 0 24 24"><path d="M6.6 10.8a15.1 15.1 0 0 0 6.6 6.6l2.2-2.2a1 1 0 0 1 1-.25 11.4 11.4 0 0 0 3.6.57 1 1 0 0 1 1 1V20a1 1 0 0 1-1 1A17 17 0 0 1 3 4a1 1 0 0 1 1-1h3.5a1 1 0 0 1 1 1c0 1.25.2 2.45.57 3.57a1 1 0 0 1-.25 1z"/></svg>
        012-345-6789
      </li>
      <li>
        <svg viewBox="0 0 24 24"><path d="M7 1h10a2 2 0 0 1 2 2v18a2 2 0 0 1-2 2H7a2 2 0 0 1-2-2V3a2 2 0 0 1 2-2zm0 3v13h10V4zm5 15.2a1.2 1.2 0 1 0 0 2.4 1.2 1.2 0 0 0 0-2.4z"/></svg>
        012-345-6789
      </li>
      <li>
        <svg viewBox="0 0 24 24"><path d="M2 5h20v14H2zm2 2v.5l8 5 8-5V7zm0 2.8V17h16V9.8l-8 5z"/></svg>
        info@velbrantix.com.com
      </li>
      <li>
        <svg viewBox="0 0 24 24"><path d="M12 2a10 10 0 1 0 0 20 10 10 0 0 0 0-20zm7.9 9h-3.4a15 15 0 0 0-1.4-6.3A8 8 0 0 1 19.9 11zM12 4c1 1.3 2.3 3.8 2.5 7h-5C9.7 7.8 11 5.3 12 4zM8.9 4.7A15 15 0 0 0 7.5 11H4.1a8 8 0 0 1 4.8-6.3zM4.1 13h3.4a15 15 0 0 0 1.4 6.3A8 8 0 0 1 4.1 13zM12 20c-1-1.3-2.3-3.8-2.5-7h5c-.2 3.2-1.5 5.7-2.5 7zm3.1-.7a15 15 0 0 0 1.4-6.3h3.4a8 8 0 0 1-4.8 6.3z"/></svg>
        www.velbrantix.com.com
      </li>
      <li class="contact__address">
        <svg viewBox="0 0 24 24"><path d="M12 1a11 11 0 1 0 0 22 11 11 0 0 0 0-22zm0 4.5a4.5 4.5 0 0 1 4.5 4.5c0 3.2-4.5 8-4.5 8s-4.5-4.8-4.5-8A4.5 4.5 0 0 1 12 5.5zm0 2.8a1.7 1.7 0 1 0 0 3.4 1.7 1.7 0 0 0 0-3.4z"/></svg>
        <span>Street Name, City Name<br>Zipcode-012345</span>
      </li>
    </ul>
  </div>
</section>

</body>
</html>
```